Business Card Design for a Personal Trainer

I need a business card design for my job as a personal trainer. It should have a unique, modern and exclusive design. On the front there should be only my logo with my name and my job. 0162/3819204 Tobias Lendhart Wiesengrundweg 14 80417 Munich Germany The most important contact information is the web adress. it can be bigger than the rest, but its not necessary. The card should be 8,5cmx5,5cm big. Font: Roboto. Colors: black, white, gray, 56c1ff.

```html
<!DOCTYPE html>
<html lang="de">
<head>
<meta charset="utf-8">
<title>Tobias Lendhart – Personal Trainer Visitenkarte</title>
<link rel="stylesheet" href="https://fonts.googleapis.com/css2?family=Roboto:wght@300;400;500&family=Roboto+Mono:wght@400;500&display=swap">
<style>
  :root {
    --backdrop: #8c8c8c;
    --card-dark: #2a2829;
    --card-light: #ffffff;
    --ink-light: #ffffff;
    --ink-dark: #333333;
    --highlight: #8f8f8f;
    --photo-top: #d9d9d9;
    --photo-bottom: #3a3a3a;
  }
  html, body {
    margin: 0;
    padding: 0;
    width: 1200px;
    height: 1200px;
    overflow: hidden;
    background: var(--backdrop);
    font-family: "Roboto", sans-serif;
  }
  .canvas {
    position: relative;
    width: 1200px;
    height: 1200px;
  }
  .card {
    position: absolute;
    left: 218px;
    width: 763px;
    height: 493px;
    overflow: hidden;
  }
  .card--front {
    top: 90px;
    background: var(--card-dark);
    color: var(--ink-light);
  }
  .card--back {
    top: 617px;
    background: var(--card-light);
    color: var(--ink-dark);
  }
  .brand-mark {
    position: absolute;
    left: 0;
    right: 0;
    top: 150px;
    display: flex;
    justify-content: center;
    align-items: center;
    gap: 16px;
  }
  .brand-mark__square {
    width: 26px;
    height: 26px;
    background: var(--ink-light);
  }
  .brand-mark__name {
    font-size: 44px;
    font-weight: 400;
    letter-spacing: 6px;
    color: var(--ink-light);
  }
  .trainer-name {
    position: absolute;
    left: 0;
    right: 0;
    top: 288px;
    margin: 0;
    text-align: center;
    font-size: 52px;
    font-weight: 400;
    letter-spacing: 1px;
    line-height: 1;
  }
  .trainer-role {
    position: absolute;
    left: 105px;
    right: 105px;
    top: 360px;
    display: flex;
    align-items: center;
    gap: 10px;
    font-size: 21px;
    font-weight: 400;
    letter-spacing: 4px;
    white-space: nowrap;
  }
  .trainer-role::before,
  .trainer-role::after {
    content: "";
    flex: 1;
    height: 2px;
    background: var(--ink-light);
  }
  .portrait {
    position: absolute;
    left: 38px;
    top: 47px;
    width: 264px;
    height: 446px;
    background: linear-gradient(180deg, var(--photo-top) 0%, #7a7a7a 35%, var(--photo-bottom) 100%);
  }
  .contact {
    position: absolute;
    left: 328px;
    top: 189px;
    margin: 0;
    padding: 0;
    list-style: none;
    font-family: "Roboto Mono", "Roboto", monospace;
    font-size: 21px;
    letter-spacing: 3px;
    line-height: 38px;
  }
  .contact__web {
    display: inline-block;
    background: var(--highlight);
    color: var(--ink-dark);
    font-weight: 500;
    padding: 0 6px 0 4px;
    line-height: 28px;
    margin-bottom: 10px;
  }
</style>
</head>
<body>
<div class="canvas">
  <section class="card card--front">
    <div class="brand-mark">
      <span class="brand-mark__square"></span>
      <span class="brand-mark__name">LENDHART</span>
    </div>
    <h1 class="trainer-name">TOBIAS LENDHART</h1>
    <div class="trainer-role">PERSONAL TRAINER</div>
  </section>

  <section class="card card--back">
    <div class="portrait" role="img" aria-label="Schwarz-Weiß-Porträt des Trainers mit verschränkten Armen"></div>
    <ul class="contact">
      <li><span class="contact__web">www.tobiaslendhart.de</span></li>
      <li>t.lendhart@mailpost.de</li>
      <li>0162/3819204</li>
      <li>Tobias Lendhart</li>
      <li>Wiesengrundweg 14</li>
      <li>80417 München</li>
    </ul>
  </section>
</div>
</body>
</html>
```